Luxury packaging graphic design for a new Hair care elixir

We need a packaging design for a new product for our line extension of hair colouring. We have already a packaging that is very well received (all in pink) including all accesories and transport box (attached files).
For a new product - protein for the hair - we need a different design tapping into luxury segment.

Target Market(s)

This product is mainly for women between 25-65 that are looking forward to improve hair strukture and make hair looks better, nicer, softer, healthier. The product in the packaging could be used up to 2x times.

Industry/Entity Type

Hair And Beauty

Font styles to use
Serif
Sans Serif

Colors

Designer to choose colors to be used in the design.

Requirements
Must have
• The material of the packaging are carton/styropor/and glass (attached a picture of packaging design to be adapted). The components are quite small so the packaging plays a big role to increase the value of what it is inside. The packaging needs to be inline with our actual packaging designs and corporate identity as they may be delivered together so as an assamble it should look nice, beautiful and of high quality.
• The graphic design for the different components to be adapted are:
• - grapich design for outside box
• - graphic design for the inside bottles
• - graphic design for the flyer/instructions inside the box
Nice to have
• It needs to feel that the packaging is Wow! It is going to be delivered per post so there have to be a beautiful opening effect. Eventually to work with colours like black, white and gold would give a nice luxury feeling.
• The actual product inside is a concentrated protein component so it is very small, therefore the packaging should show that even if small it is an elixir for the hair.
Should not have
• a totally diffenet look as our actual designs.

```html
<!DOCTYPE html>
<html lang="en">
<head>
<meta charset="utf-8">
<title>NORA VALE – Hair Elixir packaging</title>
<link rel="stylesheet" href="https://fonts.googleapis.com/css2?family=Arimo:wght@700&family=Raleway:wght@200;300&display=swap">
<style>
  :root {
    --page: #ffffff;
    --ink: #050505;
    --gold: #c9a64a;
    --gold-deep: #8a6d2a;
    --white: #ffffff;
    --grey: #9a9a9a;
  }
  * { margin: 0; padding: 0; box-sizing: border-box; }
  html, body { width: 724px; height: 1200px; overflow: hidden; background: var(--page); }
  .canvas { position: relative; width: 724px; height: 1200px; }

  .panel { position: absolute; background: var(--ink); }
  .panel__frame { position: absolute; border: 1px solid var(--gold); pointer-events: none; }

  .brand {
    position: absolute; left: 0; right: 0; text-align: center;
    font-family: "Raleway", Helvetica, sans-serif; font-weight: 300;
    color: var(--white); line-height: 1; letter-spacing: 0.06em; white-space: nowrap;
  }
  .tagline {
    position: absolute; left: 0; right: 0; text-align: center;
    font-family: "Arimo", Arial, sans-serif; font-weight: 700;
    color: var(--white); letter-spacing: 0.03em; line-height: 1; white-space: nowrap;
  }
  .product-name {
    position: absolute; left: 0; right: 0; text-align: center;
    font-family: "Raleway", Helvetica, sans-serif; font-weight: 200;
    color: var(--white); letter-spacing: 0.06em; line-height: 1;
  }
  .product-type {
    position: absolute; left: 0; right: 0; text-align: center;
    font-family: "Raleway", Helvetica, sans-serif; font-weight: 300;
    color: var(--grey); line-height: 1;
  }
  .volume {
    position: absolute; left: 0; right: 0; text-align: center;
    font-family: "Raleway", Helvetica, sans-serif; font-weight: 300;
    color: var(--gold); line-height: 1;
  }
  .hair-art {
    position: absolute;
    background: radial-gradient(ellipse at 50% 40%, var(--gold-deep) 0%, rgba(138,109,42,0.55) 45%, rgba(5,5,5,0) 78%);
  }

  /* lid */
  .lid { left: 52px; top: 40px; width: 350px; height: 355px; }
  .lid .panel__frame { inset: 10px; }
  .lid .brand { top: 148px; font-size: 40px; }
  .lid .tagline { top: 202px; font-size: 15px; }

  /* box front */
  .box-front { left: 52px; top: 418px; width: 350px; height: 739px; }
  .box-front .panel__frame { inset: 10px; }
  .box-front .hair-art { left: 12px; top: 12px; right: 12px; height: 490px; }
  .box-front .brand { top: 134px; font-size: 40px; }
  .box-front .tagline { top: 190px; font-size: 16px; }
  .box-front .product-name { top: 542px; font-size: 27px; }
  .box-front .product-type { top: 580px; font-size: 14px; }
  .box-front .volume { top: 681px; font-size: 11px; }

  /* bottle label */
  .bottle-label { left: 476px; top: 746px; width: 207px; height: 372px; }
  .bottle-label .panel__frame { inset: 7px; }
  .bottle-label .hair-art { left: 8px; top: 8px; right: 8px; height: 250px; }
  .bottle-label .brand { top: 60px; font-size: 22px; }
  .bottle-label .tagline { top: 95px; font-size: 9px; }
  .bottle-label .product-name { top: 271px; font-size: 16px; }
  .bottle-label .product-type { top: 296px; font-size: 9px; }
  .bottle-label .volume { top: 346px; font-size: 7px; }
</style>
</head>
<body>
<main class="canvas">

  <section class="panel lid" aria-label="Box lid">
    <div class="panel__frame"></div>
    <div class="brand">NORA VALE</div>
    <div class="tagline">MADE TO SHINE ON YOU</div>
  </section>

  <section class="panel box-front" aria-label="Box front">
    <div class="hair-art" role="img" aria-label="Gold line illustration of flowing wavy hair"></div>
    <div class="panel__frame"></div>
    <div class="brand">NORA VALE</div>
    <div class="tagline">MADE TO SHINE ON YOU</div>
    <div class="product-name">HAIR ELIXIR</div>
    <div class="product-type">Concentrated Serum</div>
    <div class="volume">60mL ℮</div>
  </section>

  <section class="panel bottle-label" aria-label="Bottle label">
    <div class="hair-art" role="img" aria-label="Gold line illustration of flowing wavy hair"></div>
    <div class="panel__frame"></div>
    <div class="brand">NORA VALE</div>
    <div class="tagline">MADE TO SHINE ON YOU</div>
    <div class="product-name">HAIR ELIXIR</div>
    <div class="product-type">Concentrated Serum</div>
    <div class="volume">60mL ℮</div>
  </section>

</main>
</body>
</html>
```